Upmarket Dessert Lounge needs a Business Card Design

We are an upmarket dessert lounge needing a business card to match our image.

We want something that is simple yet beautiful, feminine, classy, sophisticated and elegant. We want it to stand out and don't mind if it is bold.

The design should include our logo and colours of red or maroon with gold highlights. We don't mind if black is used.

Marlow & Quince

Target Market(s)

For those who like to indulge or treat themselves and give in to their temptations on good quality desserts.

Industry/Entity Type

Business

Requirements
Must have
• Must include our logo and our name

Marlow & Quince

M & Q

```html
<!DOCTYPE html>
<html lang="en">
<head>
<meta charset="utf-8">
<title>Marlow &amp; Quince — Business Card</title>
<link rel="stylesheet" href="https://fonts.googleapis.com/css2?family=Cormorant+Garamond:wght@500&family=Open+Sans:wght@400;700&display=swap">
<style>
  :root {
    --maroon: #7a1416;
    --cream: #f6d7a3;
    --paper: #ffffff;
    --ink: #3d3d3d;
    --stage: #ece7e1;
  }
  * { margin: 0; padding: 0; box-sizing: border-box; }
  html, body { width: 1200px; height: 402px; overflow: hidden; }
  body {
    background: var(--stage);
    position: relative;
    font-family: "Open Sans", Arial, sans-serif;
  }
  .card { position: absolute; overflow: hidden; }
  .card--front {
    left: 65px; top: 56px; width: 498px; height: 291px;
    background: var(--paper);
    box-shadow: 0 1px 3px rgba(0,0,0,.15);
  }
  .card--back {
    left: 626px; top: 56px; width: 513px; height: 300px;
    background: var(--maroon);
    display: flex; align-items: center; justify-content: center;
  }
  .brand-name {
    position: absolute; left: 32px; top: 108px; width: 216px;
    display: flex; align-items: center; justify-content: center; gap: 8px;
    font-family: "Cormorant Garamond", Georgia, serif;
    font-weight: 500; font-size: 27px; color: var(--maroon);
    white-space: nowrap;
  }
  .brand-name__dot {
    width: 10px; height: 10px; border-radius: 50%; background: var(--maroon); flex: none;
  }
  .divider {
    position: absolute; left: 287px; top: 54px; width: 2px; height: 152px;
    background: linear-gradient(to bottom, transparent, var(--maroon) 15%, var(--maroon) 85%, transparent);
  }
  .address {
    position: absolute; left: 311px; top: 64px;
    font-size: 12.5px; line-height: 16px; color: var(--ink);
  }
  .contact-list {
    position: absolute; left: 311px; top: 126px; list-style: none;
    font-size: 12.5px; line-height: 18px; color: var(--ink);
  }
  .contact-list li { display: flex; align-items: center; gap: 5px; }
  .contact-list svg { width: 10px; height: 10px; fill: var(--maroon); flex: none; }
  .wave { position: absolute; left: 0; top: 0; width: 498px; height: 291px; }
  .holder {
    position: absolute; right: 52px; bottom: 14px;
    color: var(--paper); font-size: 15px; font-weight: 700;
  }
  .holder__title { font-size: 12px; font-weight: 400; }
  .monogram {
    font-family: "Cormorant Garamond", Georgia, serif;
    font-weight: 500; font-size: 92px; color: var(--cream);
    letter-spacing: 2px;
  }
</style>
</head>
<body>
  <section class="card card--front" aria-label="Business card front">
    <svg class="wave" viewBox="0 0 498 291" aria-hidden="true">
      <path d="M0 222 C90 226 190 236 262 244 C180 246 80 240 0 238 Z" fill="var(--maroon)"/>
      <path d="M0 236 C150 272 310 250 498 232 L498 291 L0 291 Z" fill="var(--cream)"/>
      <path d="M0 250 C160 292 330 262 498 252 L498 291 L0 291 Z" fill="var(--maroon)"/>
    </svg>

    <div class="brand-name"><span class="brand-name__dot"></span>MARLOW &amp; QUINCE</div>

    <div class="divider"></div>

    <p class="address">Street Name, City Name<br>State Zip Code</p>

    <ul class="contact-list">
      <li><svg viewBox="0 0 10 10"><path d="M2 0.5 L4 2.5 L3 4 C3.6 5.3 4.7 6.4 6 7 L7.5 6 L9.5 8 L8 9.5 C4 9.2 0.8 6 0.5 2 Z"/></svg>987-654-3210</li>
      <li><svg viewBox="0 0 10 10"><path d="M2.5 0 H7.5 V10 H2.5 Z M3.5 1.5 V6 H6.5 V1.5 Z"/></svg>987-654-3210</li>
      <li><svg viewBox="0 0 10 10"><path d="M0 2 H10 V8.5 H0 Z M0.5 2.5 L5 6 L9.5 2.5" stroke="#fff" stroke-width="0.8"/></svg>info@marlowquince.com</li>
      <li><svg viewBox="0 0 10 10"><circle cx="5" cy="5" r="4.8"/><path d="M0.5 5 H9.5 M5 0.5 V9.5 M5 0.5 C2.5 3 2.5 7 5 9.5 M5 0.5 C7.5 3 7.5 7 5 9.5" stroke="#fff" stroke-width="0.6" fill="none"/></svg>www.marlowquince.com</li>
    </ul>

    <p class="holder">Your name, <span class="holder__title">Title</span></p>
  </section>

  <section class="card card--back" aria-label="Business card back">
    <span class="monogram">M &amp; Q</span>
  </section>
</body>
</html>
```